Business Card Design for Training Business

Clear Path Coaching is a new business that delivers training and other services with a focus on topics related to mental health and wellbeing, for example, Wellmind Response Course, Resilience etc. We have a strong focus on evidence-based psychology and neuroscience. I have a logo which I will upload with the brief, so please consider colours that work well with the logo.
Target Market(s)
Adults, workplaces (particularly government and not-for-profits)
Industry/Entity Type
Business
Contact Information for Business Card
Head Strong TrainingSamantha SellwoodDirector0438 770 850sam@headstrongtraining.com.auwww.headstrongtraining.com.au

```html
<!DOCTYPE html>
<html lang="en">
<head>
<meta charset="utf-8">
<title>Clear Path Coaching – Business Card</title>
<link rel="stylesheet" href="https://fonts.googleapis.com/css2?family=Roboto:wght@300;400;700&display=swap">
<style>
  :root {
    --backdrop: #e9e6e2;
    --card: #ffffff;
    --teal: #4fbcbc;
    --teal-soft: #cfe7e6;
    --ink: #161616;
    --brand-grey: #7d7672;
  }
  html, body {
    margin: 0;
    width: 1200px;
    height: 960px;
    overflow: hidden;
    background: var(--backdrop);
    font-family: "Roboto", Arial, sans-serif;
  }
  .business-card {
    position: absolute;
    left: 140px;
    top: 200px;
    width: 920px;
    height: 560px;
    background: var(--card);
    box-shadow: 0 14px 34px rgba(0,0,0,0.18);
    overflow: hidden;
  }
  .decor-area {
    position: absolute;
    left: -40px;
    top: 120px;
    width: 560px;
    height: 480px;
    background: radial-gradient(closest-side, rgba(255,255,255,0) 35%, var(--teal-soft) 75%, rgba(255,255,255,0) 100%);
    opacity: 0.8;
  }
  .brand {
    position: absolute;
    right: 70px;
    top: 60px;
    display: flex;
    align-items: center;
    gap: 14px;
  }
  .brand-dot {
    width: 22px;
    height: 22px;
    border-radius: 50%;
    background: var(--teal);
  }
  .brand-name {
    font-weight: 300;
    font-size: 30px;
    letter-spacing: 2px;
    color: var(--brand-grey);
    text-transform: uppercase;
  }
  .person {
    position: absolute;
    right: 70px;
    top: 190px;
    text-align: right;
  }
  .person-name {
    margin: 0;
    font-weight: 700;
    font-size: 34px;
    color: var(--teal);
  }
  .person-role {
    margin: 2px 0 0;
    font-weight: 700;
    font-size: 22px;
    color: var(--ink);
  }
  .contact-list {
    position: absolute;
    right: 70px;
    top: 320px;
    margin: 0;
    padding: 0;
    list-style: none;
    text-align: right;
  }
  .contact-item {
    display: flex;
    justify-content: flex-end;
    align-items: center;
    gap: 20px;
    font-weight: 400;
    font-size: 25px;
    color: var(--ink);
    line-height: 46px;
  }
  .contact-icon {
    width: 20px;
    height: 20px;
    flex: none;
  }
</style>
</head>
<body>
  <main class="business-card">
    <div class="decor-area" role="img" aria-label="Large faint teal decorative pattern"></div>

    <div class="brand">
      <span class="brand-dot"></span>
      <span class="brand-name">Clear Path Coaching</span>
    </div>

    <div class="person">
      <p class="person-name">Rebecca Tanfield</p>
      <p class="person-role">Director</p>
    </div>

    <ul class="contact-list">
      <li class="contact-item">
        <span>0491 362 517</span>
        <svg class="contact-icon" viewBox="0 0 20 20" aria-hidden="true">
          <rect width="20" height="20" fill="#161616"/>
          <path d="M6 4 L8 4 L9 7 L7.5 8.5 Q9 11.5 11.5 12.5 L13 11 L16 12 L16 14 Q15 16 13 16 Q6 14 4 7 Q4 5 6 4 Z" fill="#fff"/>
        </svg>
      </li>
      <li class="contact-item">
        <span>bec@clearpathcoaching.example.au</span>
        <svg class="contact-icon" viewBox="0 0 20 20" aria-hidden="true">
          <rect width="20" height="20" fill="#161616"/>
          <rect x="4" y="6" width="12" height="8" fill="none" stroke="#fff" stroke-width="1.5"/>
          <path d="M4 6 L10 11 L16 6" fill="none" stroke="#fff" stroke-width="1.5"/>
        </svg>
      </li>
      <li class="contact-item">
        <span>www.clearpathcoaching.example.au</span>
        <svg class="contact-icon" viewBox="0 0 20 20" aria-hidden="true">
          <rect width="20" height="20" fill="#161616"/>
          <circle cx="10" cy="10" r="5.5" fill="none" stroke="#fff" stroke-width="1.5"/>
          <path d="M4.5 10 H15.5 M10 4.5 Q7 10 10 15.5 M10 4.5 Q13 10 10 15.5" fill="none" stroke="#fff" stroke-width="1.2"/>
        </svg>
      </li>
    </ul>
  </main>
</body>
</html>
```